Web Design Project

Psychotherapy and Counselling Practice needs a landing page web design.

My business "Larkfield Advisory" specialises in the treatment of Anxiety and Depression with a holistic approach, endeavouring to unlock the key that holds us to ransom in a life that is imbalanced, frustrating, and ultimately of our own making due to our own perceptions and behaviours.

There is much that impacts us which we cannot change, but we are always in control of how we think, and how we frame our experiences.....learning to challenge those thoughts and behaviours that are destructive and disempowering opens up a world of joyful possibility. Life is about making choices, learn to make wiser and healthier choices.......

Larkfield Advisory has a client base of individual clients but will seek to expand to offer services to the Corporate world by offering an adjunct to employers for established "Wellness Programs".

Larkfield Advisory is a highly professional, ethically bound business, with the needs of the client at the forefront of all we do.

Larkfield Advisory wishes to avoid the usual "jargon driven" psychobabble offered on many counselling web pages. It aims to be stylishly presented, clean in look and with as few "words" as possible and a largely white background (faster loading and more powerful impact of what is stated), those words contained in the webpage should be meaningful, persuasive and have an impact simply at glance. Larkfield does not want , or expect, those prospective clients in need of support , to be reading through volumes of industry driven cliches.

At this point Larkfield is just looking for a high quality landing page. However in time this will likely expand to include other sections such as case studies, video content etc.

Target Market(s)

Those in need of emotional support, suffering mental health issues, and those simply wanting to become self aware supported by a mindful therapist.

Industry/Entity Type

Industry

Requirements
Must have
• The design must incorporate the Larkfield logo and colour schemes found on the attached files.

```html
<!DOCTYPE html>
<html lang="en">
<head>
<meta charset="utf-8">
<title>Larkfield Advisory</title>
<link rel="stylesheet" href="https://fonts.googleapis.com/css2?family=Open+Sans:wght@700&display=swap">
<style>
  :root {
    --leaf: #8cb43a;
    --leaf-deep: #7c9e24;
    --slate: #6f6f6f;
    --slate-dark: #555555;
    --ink-soft: #8c8c8c;
    --ink: #7a7a7a;
    --paper: #ffffff;
    --tile-text: #e2e2e2;
  }
  html, body {
    margin: 0;
    padding: 0;
    overflow: hidden;
    background: var(--paper);
  }
  .page {
    position: relative;
    width: 1200px;
    height: 891px;
    overflow: hidden;
    background: var(--paper);
    font-family: "Open Sans", Arial, sans-serif;
    font-weight: 700;
  }
  .brand-tile {
    position: absolute;
    left: 619px;
    top: 60px;
    width: 134px;
    height: 133px;
    border-radius: 4px;
    background: var(--slate);
    display: flex;
    align-items: center;
    justify-content: center;
    color: var(--tile-text);
    font-size: 17px;
    letter-spacing: 1px;
  }
  .contact {
    position: absolute;
    left: 764px;
    top: 56px;
    color: var(--ink-soft);
    letter-spacing: 3.2px;
  }
  .contact__name {
    margin: 0;
    font-size: 21px;
    letter-spacing: 4px;
    line-height: 28px;
  }
  .contact__quals {
    margin: 4px 0 0;
    font-size: 15px;
    line-height: 20px;
  }
  .contact__lines {
    margin: 38px 0 0;
    font-size: 15px;
    line-height: 26px;
  }
  .wordmark {
    position: absolute;
    left: 80px;
    top: 461px;
    margin: 0;
    font-size: 80px;
    line-height: 90px;
    letter-spacing: 2px;
    color: var(--leaf);
  }
  .motto {
    position: absolute;
    left: 740px;
    top: 377px;
    width: 420px;
    margin: 0;
    text-align: center;
    color: var(--ink);
    font-size: 16px;
    line-height: 26px;
    letter-spacing: 3px;
  }
  .promise {
    position: absolute;
    left: 594px;
    top: 601px;
    margin: 0;
    height: 50px;
    display: flex;
    align-items: center;
    font-size: 16px;
    letter-spacing: 3px;
    color: var(--ink-soft);
    white-space: nowrap;
  }
  .promise__badge {
    width: 180px;
    height: 50px;
    border-radius: 2px;
    background: var(--slate-dark);
    display: flex;
    align-items: center;
    justify-content: center;
    color: var(--leaf);
    font-size: 26px;
    letter-spacing: 0;
  }
  .promise__accent {
    color: var(--leaf-deep);
    margin: 0 8px 0 2px;
  }
  .ground {
    position: absolute;
    left: 0;
    top: 700px;
    width: 1200px;
    height: 140px;
  }
  .site-link {
    position: absolute;
    left: 766px;
    top: 847px;
    margin: 0;
    color: var(--leaf-deep);
    font-size: 16px;
    letter-spacing: 3px;
  }
</style>
</head>
<body>
<main class="page">
  <div class="brand-tile">Larkfield</div>

  <section class="contact">
    <h2 class="contact__name">MARA ELLISON</h2>
    <p class="contact__quals">BA (Psych) BSc (Hons) Psych MBPS</p>
    <p class="contact__lines">Mobile: 0400 318 726<br>E-mail: mara.ellison@larkmail.net</p>
  </section>

  <h1 class="wordmark">LARKFIELD</h1>

  <p class="motto">“Life is about making choices,<br>learn to make Wiser<br>and Healthier choices”.</p>

  <p class="promise">
    <span class="promise__badge">Larkfield</span>
    <span class="promise__accent">Advisory</span>
    is highly Professional
  </p>

  <svg class="ground" viewBox="0 700 1200 140" aria-hidden="true">
    <path d="M0 765 C300 790 700 770 1200 738 L1200 830 L0 830 Z" fill="var(--slate)"/>
    <path d="M0 728 C300 742 700 742 1080 731 C700 752 320 768 0 762 Z" fill="var(--leaf)"/>
  </svg>

  <p class="site-link">www.larkfieldadvisory.com.au</p>
</main>
</body>
</html>
```